Yacht, Boats, Watersports company needs a redesign of business card

Hello Designers!
We are a Boat dealership company that sells fun in the water, we sell boats, Yachts, Kayaks and also yacht WaterSport toys. We are looking to redesign our business cards in to something a little bit more sophisticated. in a way that we can make better use of our company colors. I'm attaching a zipped file containing the company 3 sets of company logo which one is an horizontal another one is a vertical and also a chromed 3d logo. Also is included two set of business cards that we use and also some designs that i think it's interesting. We use PMS 2026c Orange and PMS 7687C Blue. I would like to see at least two different options with the orange as accent and also using blue as an accent color. It's really important for the business cards to have a font option and size that is legible to most people. Our current website is wwww.coralpennant.com. Please visit if you want to have a better feeling of the Boat dealership
You can send Single sided or double side options. We are now using single sided but we may be open for a double side option if we really like the design.
Target Market(s)
Marine, boat sales, yacht sales, water toys sales/
Contact Information for Business Card
Name: Dale Whitcombe
Address: 212 North Fenwick Lane,
Harbor Point, FL 33019
Phone: 954-731-8842
Fax: 954:731-8843
Cell: 954-382-1490
Email: dw@coralpennant.com
Website: coralpennant.com
Requirements
Must have
- the current information of the business card provided.
logo
use the PMS Colors
Nice to have
- a touch of elegance and sophistication but simple
Should not have
- should not have any typography that is hard to read, the card should be simple but yet sophisticated.

```html
<!DOCTYPE html>
<html lang="en">
<head>
<meta charset="utf-8">
<title>Coral Pennant – Business Card</title>
<link rel="stylesheet" href="https://fonts.googleapis.com/css2?family=Roboto:wght@400;500;700&display=swap">
<style>
  :root {
    --navy: #143f74;
    --navy-deep: #0f3462;
    --orange: #f0622c;
    --white: #ffffff;
    --backdrop: #e9ebee;
  }
  * { box-sizing: border-box; margin: 0; padding: 0; }
  html, body { width: 1200px; height: 900px; overflow: hidden; }
  body {
    background: var(--backdrop);
    font-family: "Roboto", Arial, sans-serif;
    position: relative;
  }
  .card {
    position: absolute;
    width: 620px;
    height: 354px;
    border-radius: 22px;
    overflow: hidden;
    box-shadow: 0 10px 30px rgba(15, 30, 60, 0.25);
  }
  .card-front {
    left: 60px; top: 70px;
    background: linear-gradient(135deg, #1a4a85 0%, var(--navy) 55%, var(--navy-deep) 100%);
  }
  .front-brand {
    position: absolute;
    left: 0; right: 0; top: 112px;
    display: flex; align-items: center; justify-content: center; gap: 16px;
  }
  .brand-mark {
    width: 46px; height: 46px; border-radius: 50%;
    border: 5px solid var(--white);
  }
  .brand-name {
    font-weight: 700;
    text-transform: uppercase;
    letter-spacing: 4px;
    font-size: 34px;
    color: var(--white);
  }
  .front-url {
    position: absolute; left: 0; right: 0; top: 210px;
    text-align: center;
    color: var(--white);
    font-size: 17px;
    letter-spacing: 4px;
  }
  .card-back {
    left: 520px; top: 470px;
    background: var(--white);
  }
  .card-back svg.back-shape { position: absolute; inset: 0; }
  .back-brand {
    position: absolute; left: 0; right: 0; top: 28px;
    display: flex; flex-direction: column; align-items: center; gap: 12px;
  }
  .back-brand .brand-mark { border-color: var(--orange); width: 52px; height: 52px; }
  .back-brand .brand-name { color: var(--navy); font-size: 28px; }
  .holder {
    position: absolute; left: 40px; top: 250px;
    color: var(--white);
  }
  .holder-name {
    color: var(--orange);
    font-weight: 700;
    font-size: 22px;
    text-transform: uppercase;
    margin-bottom: 6px;
  }
  .holder-address { font-size: 16px; line-height: 21px; }
  .divider {
    position: absolute; left: 318px; top: 224px;
    width: 1px; height: 112px;
    background: rgba(255, 255, 255, 0.7);
  }
  .contact-list {
    position: absolute; left: 338px; top: 206px;
    list-style: none;
    color: var(--white);
    font-size: 16px;
  }
  .contact-list li { display: flex; align-items: center; gap: 10px; height: 26px; }
  .contact-list svg { width: 15px; height: 15px; flex: none; }
</style>
</head>
<body>

<section class="card card-front" aria-label="Business card front">
  <div class="front-brand">
    <span class="brand-mark" aria-hidden="true"></span>
    <span class="brand-name">Coral Pennant</span>
  </div>
  <p class="front-url">www.coralpennant.com</p>
</section>

<section class="card card-back" aria-label="Business card back">
  <svg class="back-shape" width="620" height="354" viewBox="0 0 620 354" aria-hidden="true">
    <defs>
      <linearGradient id="swoosh" x1="0" x2="1" y1="0" y2="0">
        <stop offset="0" stop-color="#e9531f"/>
        <stop offset="1" stop-color="#f37a3e"/>
      </linearGradient>
      <linearGradient id="sea" x1="0" x2="1" y1="1" y2="0">
        <stop offset="0" stop-color="#123a6c"/>
        <stop offset="1" stop-color="#1a4a85"/>
      </linearGradient>
    </defs>
    <path d="M0,212 C200,200 440,165 620,60 L620,78 C440,178 200,214 0,222 Z" fill="url(#swoosh)"/>
    <path d="M0,222 C200,214 440,178 620,78 L620,354 L0,354 Z" fill="url(#sea)"/>
  </svg>

  <div class="back-brand">
    <span class="brand-mark" aria-hidden="true"></span>
    <span class="brand-name">Coral Pennant</span>
  </div>

  <div class="holder">
    <p class="holder-name">Dale Whitcombe</p>
    <p class="holder-address">212 North Fenwick Lane,<br>Harbor Point, FL 33019</p>
  </div>

  <div class="divider"></div>

  <ul class="contact-list">
    <li>
      <svg viewBox="0 0 16 16" aria-label="Phone"><path d="M4 1l3 3-2 2c1 2 3 4 5 5l2-2 3 3-2 2C7 14 2 9 2 3z" fill="#fff"/></svg>
      954-731-8842
    </li>
    <li>
      <svg viewBox="0 0 16 16" aria-label="Fax"><rect x="4" y="1" width="8" height="5" fill="none" stroke="#fff" stroke-width="1.5"/><rect x="1" y="6" width="14" height="8" rx="1" fill="#fff"/></svg>
      954:731-8843
    </li>
    <li>
      <svg viewBox="0 0 16 16" aria-label="Mobile"><rect x="4" y="1" width="8" height="14" rx="1.5" fill="none" stroke="#fff" stroke-width="1.5"/><circle cx="8" cy="12.5" r="1" fill="#fff"/></svg>
      954-382-1490
    </li>
    <li>
      <svg viewBox="0 0 16 16" aria-label="Email"><rect x="1" y="3" width="14" height="10" fill="none" stroke="#fff" stroke-width="1.5"/><path d="M1 3l7 6 7-6" fill="none" stroke="#fff" stroke-width="1.5"/></svg>
      dw@coralpennant.com
    </li>
    <li>
      <svg viewBox="0 0 16 16" aria-label="Website"><circle cx="8" cy="8" r="6.5" fill="none" stroke="#fff" stroke-width="1.3"/><ellipse cx="8" cy="8" rx="3" ry="6.5" fill="none" stroke="#fff" stroke-width="1.1"/><path d="M1.5 8h13M2.5 5h11M2.5 11h11" stroke="#fff" stroke-width="1"/></svg>
      www.coralpennant.com
    </li>
  </ul>
</section>

</body>
</html>
```